Jolly Paws Business Card Update

I have a business card which I love. I want to keep the same logo, colours, font and style. I want to upgrade the scripting and remove some elements and add others.
On the front side under Services - remove the existing wording and insert - Providing individual coaching strategies to create happy, healthy and social canine companions
Under Denise Carvell amend the current wording to read: Qualified in Dog Behavioural Training, Natural Animal Healthcare and Animal Health Science
On the reverse side to remove the web address.

```html
<!DOCTYPE html>
<html lang="en">
<head>
<meta charset="utf-8">
<title>Jolly Paws Business Card</title>
<link rel="stylesheet" href="https://fonts.googleapis.com/css2?family=Arimo:wght@400;700&family=Open+Sans:ital,wght@0,400;0,600;1,400&display=swap">
<style>
  :root {
    --bg: #2b2b2d;
    --blue-light: #0a8fd0;
    --blue-mid: #1f5bb0;
    --blue-deep: #2b3584;
    --cream: #efe9d6;
    --red: #b81d24;
    --red-dark: #8f1419;
    --white: #ffffff;
    --text-soft: #e6ecf6;
  }
  * { margin: 0; padding: 0; box-sizing: border-box; }
  html, body { width: 1200px; height: 1138px; overflow: hidden; }
  body { background: var(--bg); position: relative; font-family: "Open Sans", sans-serif; }

  .card {
    position: absolute;
    left: 288px;
    width: 624px;
    height: 376px;
    border-radius: 16px;
    overflow: hidden;
  }
  .card--front {
    top: 186px;
    background: linear-gradient(180deg, var(--blue-light) 0%, var(--blue-mid) 55%, var(--blue-deep) 100%);
  }
  .card--back {
    top: 608px;
    background: linear-gradient(225deg, var(--blue-light) 0%, var(--blue-mid) 55%, var(--blue-deep) 100%);
  }

  .brand-dot {
    position: absolute;
    border-radius: 50%;
    background: var(--cream);
  }
  .card--front .brand-dot { left: 236px; top: 74px; width: 152px; height: 152px; }
  .card--back .brand-dot { left: 34px; top: 40px; width: 112px; height: 112px; }

  .brand-name {
    position: absolute;
    font-family: "Arimo", sans-serif;
    font-weight: 700;
    color: var(--cream);
    letter-spacing: 1px;
    white-space: nowrap;
  }
  .card--front .brand-name { left: 0; width: 624px; text-align: center; top: 226px; font-size: 42px; line-height: 48px; }
  .card--back .brand-name { left: 170px; top: 58px; font-size: 40px; line-height: 46px; }

  .tagline {
    position: absolute;
    font-family: "Arimo", sans-serif;
    color: var(--text-soft);
    white-space: nowrap;
    font-size: 19px;
    line-height: 22px;
  }
  .card--front .tagline { left: 0; width: 624px; text-align: center; top: 276px; }
  .card--back .tagline { left: 170px; top: 108px; }

  .services {
    position: absolute;
    left: 92px;
    width: 440px;
    top: 312px;
    text-align: center;
    font-size: 13.5px;
    line-height: 19px;
    color: var(--text-soft);
  }

  .person { position: absolute; left: 30px; top: 198px; color: var(--white); }
  .person__name { font-weight: 600; font-size: 24px; line-height: 30px; }
  .person__role { font-style: italic; font-size: 15.5px; line-height: 21px; color: var(--text-soft); }

  .contacts { position: absolute; left: 348px; top: 204px; list-style: none; color: var(--text-soft); }
  .contacts li { display: flex; align-items: center; height: 23px; font-size: 15.5px; }
  .contacts svg { width: 14px; height: 14px; margin-right: 13px; fill: var(--text-soft); }

  .motto { position: absolute; left: 30px; top: 325px; font-family: "Arimo", sans-serif; font-size: 16.5px; line-height: 20px; color: var(--white); }

  .footer-band { position: absolute; left: 0; bottom: 0; width: 624px; height: 48px; }
  .footer-text {
    position: absolute; left: 282px; top: 339px;
    font-family: "Arimo", sans-serif; font-size: 16.5px; line-height: 20px; color: var(--white); white-space: nowrap;
  }
</style>
</head>
<body>

<section class="card card--front">
  <div class="brand-dot"></div>
  <div class="brand-name">JOLLY PAWS</div>
  <div class="tagline">HAPPY DOGS, HAPPY OWNERS</div>
  <p class="services">Providing individual coaching strategies to create happy, healthy and social canine companions</p>
</section>

<section class="card card--back">
  <div class="brand-dot"></div>
  <div class="brand-name">JOLLY PAWS</div>
  <div class="tagline">HAPPY DOGS, HAPPY OWNERS</div>

  <div class="person">
    <div class="person__name">Denise Carvell</div>
    <div class="person__role">Qualified in Dog Behavioural Training,<br>Natural Animal Healthcare and<br>Animal Health Science</div>
  </div>

  <ul class="contacts">
    <li><svg viewBox="0 0 14 14"><path d="M3.5 0h7v14h-7z M4.5 1.2v4h5v-4z M4.6 6.5h1.3v1.2H4.6z M6.4 6.5h1.3v1.2H6.4z M8.2 6.5h1.3v1.2H8.2z M4.6 8.4h1.3v1.2H4.6z M6.4 8.4h1.3v1.2H6.4z M8.2 8.4h1.3v1.2H8.2z M4.6 10.3h1.3v1.2H4.6z M6.4 10.3h1.3v1.2H6.4z M8.2 10.3h1.3v1.2H8.2z" fill-rule="evenodd"/></svg>0412 667 205</li>
    <li><svg viewBox="0 0 14 14"><path d="M0 3h14v1L7 8.5 0 4z M0 5.3l7 4.5 7-4.5V11H0z"/></svg>jollypaws1@mail.com</li>
  </ul>

  <div class="motto">Promoting Communication</div>

  <svg class="footer-band" viewBox="0 0 624 48" preserveAspectRatio="none">
    <defs>
      <linearGradient id="redBand" x1="0" y1="0" x2="1" y2="0">
        <stop offset="0" stop-color="#8f1419"/>
        <stop offset="0.4" stop-color="#b81d24"/>
        <stop offset="1" stop-color="#b81d24"/>
      </linearGradient>
    </defs>
    <polygon points="0,36 262,36 256,48 0,48" fill="#efe9d6"/>
    <polygon points="276,0 624,0 624,48 256,48" fill="url(#redBand)"/>
  </svg>
  <div class="footer-text">Connection between dogs &amp; their families</div>
</section>

</body>
</html>
```